Harbourline Electrical Solutions

On one side. LOGO (underneath:) Commercial Industrial Residential

- NAME & CONTACT DETAILS

Marcus T. Hollings
Project Manager

(Cell icon) (441) 555-0187
(Email icon) hlelectricalsolutions@mailvento.com
(Facebook & Instagram icons )@hlelectricalsolutions

Other side: LOGO - underneath ELECTRICAL CONSTRUCTION & MAINTENANCE . LED LIGHTING & AUTOMATION . LIFE SAFETY SYSTEMS (FIRE ALARM / SECURITY) . DATA & COMMUNICATION

```html
<!DOCTYPE html>
<html lang="en">
<head>
<meta charset="utf-8">
<title>Harbourline Electrical Solutions – Business Card</title>
<link rel="stylesheet" href="https://fonts.googleapis.com/css2?family=Montserrat:wght@400;500;600;700&family=Lato:wght@400;700&display=swap">
<style>
  :root {
    --teal: #135a6e;
    --charcoal: #4a4a4a;
    --paper: #ffffff;
    --ink-grey: #5a5a5a;
    --stage: #e6e7e9;
  }
  * { box-sizing: border-box; margin: 0; padding: 0; }
  html, body { width: 1200px; height: 1015px; overflow: hidden; }
  body {
    background: var(--stage);
    font-family: "Montserrat", sans-serif;
    position: relative;
  }
  .card {
    position: absolute;
    left: 190px;
    width: 820px;
    height: 469px;
    overflow: hidden;
    box-shadow: 0 6px 18px rgba(0,0,0,.18);
  }

  /* Services side */
  .card--services { top: 25px; background: var(--teal); }
  .services__brand {
    position: absolute; left: 0; right: 0; top: 110px;
    display: flex; justify-content: center; align-items: center; gap: 18px;
  }
  .brand-square { width: 22px; height: 22px; background: var(--paper); }
  .brand-name {
    font-weight: 600; font-size: 30px; letter-spacing: 3px;
    text-transform: uppercase; color: var(--paper);
  }
  .services__band {
    position: absolute; left: 0; right: 0; top: 272px; height: 142px;
    background: var(--charcoal);
    display: flex; flex-direction: column; justify-content: center; align-items: center;
    gap: 6px;
  }
  .services__line {
    color: var(--paper); font-weight: 500; font-size: 17px;
    letter-spacing: 1.2px; text-transform: uppercase;
  }

  /* Contact side */
  .card--contact { top: 521px; background: var(--paper); }
  .contact__person { position: absolute; left: 62px; top: 172px; }
  .person-name {
    color: var(--teal); font-weight: 700; font-size: 27px;
    letter-spacing: .5px; text-transform: uppercase;
  }
  .person-role { color: var(--ink-grey); font-family: "Lato", sans-serif; font-size: 21px; margin-top: 2px; }

  .contact__brand { position: absolute; right: 46px; top: 86px; text-align: left; }
  .contact__brand .brand-row { display: flex; align-items: center; gap: 12px; }
  .contact__brand .brand-square { background: var(--teal); width: 18px; height: 18px; }
  .contact__brand .brand-name { color: var(--teal); font-size: 23px; letter-spacing: 2px; }
  .brand-tagline {
    margin-top: 12px; color: var(--ink-grey); font-family: "Lato", sans-serif;
    font-size: 17px; letter-spacing: 1.5px; text-transform: uppercase; text-align: right;
  }

  .contact__social {
    position: absolute; right: 40px; top: 300px;
    display: flex; align-items: center; gap: 8px;
    color: var(--ink-grey); font-family: "Lato", sans-serif; font-size: 19px;
  }
  .social-dot { width: 18px; height: 18px; border: 2px solid var(--teal); border-radius: 50%; }

  .contact__details {
    position: absolute; left: 62px; bottom: 48px; list-style: none;
    font-family: "Lato", sans-serif; font-size: 21px; color: var(--ink-grey);
  }
  .contact__details li { display: flex; align-items: center; gap: 10px; line-height: 1.45; }
  .contact__details svg { width: 20px; height: 20px; flex: none; }

  .contact__bar-grey {
    position: absolute; left: 0; bottom: 0; width: 70%; height: 18px; background: var(--charcoal);
  }
  .contact__bar-teal {
    position: absolute; right: 0; bottom: 0; width: 31%; height: 56px; background: var(--teal);
  }
</style>
</head>
<body>

<section class="card card--services" aria-label="Card back: services">
  <div class="services__brand">
    <span class="brand-square"></span>
    <span class="brand-name">Harbourline Electrical Solutions</span>
  </div>
  <div class="services__band">
    <p class="services__line">Electrical Construction &amp; Maintenance</p>
    <p class="services__line">LED Lighting &amp; Automation | Data &amp; Communication</p>
    <p class="services__line">Life Safety Systems (Fire Alarm / Security)</p>
  </div>
</section>

<section class="card card--contact" aria-label="Card front: contact">
  <div class="contact__brand">
    <div class="brand-row">
      <span class="brand-square"></span>
      <span class="brand-name">Harbourline Electrical Solutions</span>
    </div>
    <p class="brand-tagline">Commercial Industrial Residential</p>
  </div>

  <div class="contact__person">
    <h1 class="person-name">Marcus T. Hollings</h1>
    <p class="person-role">Project Manager</p>
  </div>

  <div class="contact__social">
    <span class="social-dot"></span>
    <span>@hlelectricalsolutions</span>
  </div>

  <ul class="contact__details">
    <li>
      <svg viewBox="0 0 20 20" aria-hidden="true"><rect x="3" y="1.5" width="14" height="17" rx="2" fill="none" stroke="#135a6e" stroke-width="2"/><rect x="5.5" y="4" width="9" height="10" fill="#135a6e"/></svg>
      <span>(441) 555-0187</span>
    </li>
    <li>
      <svg viewBox="0 0 20 20" aria-hidden="true"><rect x="1" y="4" width="18" height="12" fill="#135a6e"/><path d="M1.5 4.5 10 11l8.5-6.5" fill="none" stroke="#fff" stroke-width="1.6"/></svg>
      <span>hlelectricalsolutions@mailvento.com</span>
    </li>
  </ul>

  <div class="contact__bar-grey"></div>
  <div class="contact__bar-teal"></div>
</section>

</body>
</html>
```